Website redesign for KestrelFinanceMan/TKFinanceMan

Job Title: Talented Web Designer for SEO-Friendly Website Creation & HostFalcon cPanel Integration
 
Inspiration: dunewheelracingexample.com
Pages:

About
Get a Quote
FAQ
Boat Loans
RV Loans
Testimonials
News/Blog
Affiliate Program
Contact

Job Description:
 
We are seeking a skilled and creative freelance web designer to build a stunning, SEO-optimized website for our business. The ideal candidate will have a strong design portfolio, technical expertise in creating search engine-friendly websites, and experience implementing websites into HostFalcon cPanel.
 
Project Overview:
 
Objective: Create a modern, motorsports themed visually appealing website that is optimized for SEO.

Platform: The site will be hosted on HostFalcon, so familiarity with their cPanel for setup and integration is essential.

Deliverables:
         •A fully functional website (desktop and mobile) with user-friendly navigation and a responsive design.
         •SEO best practices implemented throughout, including proper meta tags, optimized images, fast loading speeds, and mobile compatibility.
         •Seamless integration into HostFalcon cPanel for hosting.
         •Guidance or documentation on maintaining the site post-launch.
 
Key Skills Required:
 
         •Proficiency in web design (HTML, CSS, JavaScript, or relevant platforms like WordPress).
         •Knowledge of SEO principles and tools for website optimization.
         •Experience with HostFalcon cPanel, including file management and DNS settings.
         •Strong communication skills to understand our vision and provide progress updates.
 
What We’re Looking For:
 
         •A designer who can transform our ideas into a sleek and functional website.
         •Someone proactive in suggesting creative design elements and SEO improvements.
         •A reliable professional who can meet deadlines and deliver a polished product.
 
Please provide:
 
         1.A brief introduction and why you’re a good fit for this project.
         2.Examples of previous web design projects, especially those with SEO implementation.
         3.Your estimated timeline and cost for this project.
 
We are excited to work with a talented designer who can bring our vision to life. If you are passionate about web design and SEO, we’d love to hear from you!

Target Market(s)

Boat and RV buyers looking for a loan

Coding

Coded - Design and coding required

Number of Pages Required

5+ page

Colors
F0912C
F2A743
F7CA91
FBE8D2
FDF5EE

Requirements
Must have
• motorsports type design
Nice to have
• fcontact forms easy to use layout on brand and color scheme of kestrelfinanceman and tkfinanceman.example

```html
<!DOCTYPE html>
<html lang="en">
<head>
<meta charset="utf-8">
<title>TKFinanceMan – RV Loans Made Easy</title>
<link href="https://fonts.googleapis.com/css2?family=Barlow+Condensed:ital,wght@1,800&family=Poppins:wght@400;500;600;700&display=swap" rel="stylesheet">
<style>
:root{
  --orange:#F47A12;
  --orange-deep:#EE5F06;
  --orange-soft:#F2A743;
  --peach:#F7CA91;
  --cream:#FDF5EE;
  --ink:#111111;
  --dark:#262626;
  --grey-bg:#F3F3F3;
  --text:#333333;
  --white:#ffffff;
}
*{margin:0;padding:0;box-sizing:border-box}
html,body{width:1200px;height:4461px;overflow:hidden}
body{position:relative;font-family:'Poppins',sans-serif;color:var(--text);background:var(--white)}
.abs{position:absolute}
.display{font-family:'Barlow Condensed',sans-serif;font-style:italic;font-weight:800;text-transform:uppercase;color:var(--ink);letter-spacing:-0.5px;line-height:1}
.btn{position:absolute;display:flex;align-items:center;justify-content:center;background:var(--orange);color:var(--white);font-weight:600;font-size:14px}
.logo{font-family:'Poppins',sans-serif;font-weight:700;color:var(--orange);font-size:30px;display:flex;align-items:center;gap:10px}
.logo .mark{width:16px;height:16px;background:var(--orange);border-radius:50%}

/* top bar + nav */
.topbar{left:0;top:0;width:1200px;height:33px;background:linear-gradient(90deg,var(--orange-deep),var(--orange-soft));color:var(--white);font-size:12px;font-weight:600}
.topbar .left{left:144px;top:8px}
.topbar .right{right:144px;top:8px;display:flex;gap:8px;align-items:center}
.nav{left:0;top:33px;width:1200px;height:64px;background:var(--ink)}
.nav .logo{left:144px;top:14px}
.nav-links{left:466px;top:0;height:64px;display:flex;gap:28px;align-items:center;font-size:14px;font-weight:600;color:var(--white)}
.nav-links .active{color:var(--orange);position:relative}
.nav-links .active::after{content:"";position:absolute;left:0;right:0;bottom:-20px;height:3px;background:var(--orange)}
.nav .btn{left:940px;top:12px;width:116px;height:35px}

/* hero */
.hero{left:0;top:97px;width:1200px;height:600px;overflow:hidden}
.hero-photo{left:0;top:0;width:1200px;height:600px;background:linear-gradient(180deg,#c9772a 0%,#e3953a 100%)}
.hero-rv{left:667px;top:-5px;width:606px;height:606px;border-radius:50%;background:linear-gradient(180deg,#d7dde4 0%,#a9b3bd 100%)}
.hero h1{left:144px;top:95px;font-size:70px;color:var(--ink)}
.hero p{left:144px;top:250px;width:470px;font-size:16px;line-height:24px;color:#111}
.hero .btn{left:144px;top:313px;width:124px;height:36px}
.arrow{position:absolute;border-radius:50%;background:var(--white);display:flex;align-items:center;justify-content:center}
.arrow.line{background:transparent;border:2px solid var(--white)}
.arrow.dark{background:transparent;border:1.5px solid #333}

/* trusted */
.trusted-img{left:140px;top:807px;width:440px;height:440px;border-radius:50%;background:linear-gradient(180deg,#d9dfe6 0%,#a3adb7 100%)}
.trusted h2{left:632px;top:786px;font-size:46px}
.ticks{left:630px;top:890px;list-style:none;font-size:14px;color:#222}
.ticks li{height:32px;display:flex;align-items:center;gap:12px}
.trusted p{left:630px;top:1090px;width:430px;font-size:14px;line-height:24px;color:#222}
.trusted .btn{left:630px;top:1207px;width:125px;height:35px}

/* rv types */
.types{left:0;top:1320px;width:1200px;height:620px}
.types h2{left:0;top:195px;width:1200px;text-align:center;font-size:46px;color:var(--white)}
.type{position:absolute;top:277px;width:184px;text-align:center}
.type .pic{width:184px;height:184px;border-radius:50%}
.type span{display:block;margin-top:20px;color:var(--white);font-weight:600;font-size:20px}

/* more than boats */
.more{left:0;top:1936px;width:1200px;height:471px;background:var(--grey-bg)}
.more h2{left:145px;top:92px;font-size:46px;width:400px}
.more p{left:551px;top:92px;width:520px;font-size:17px;line-height:32px;color:#222}
.more .btn{left:551px;top:161px;width:124px;height:37px}
.card{position:absolute;top:2175px;width:284px;height:312px;background:var(--white);border-radius:14px;box-shadow:0 4px 18px rgba(0,0,0,.12);text-align:center}
.card .pic{margin:12px auto 0;width:256px;height:221px;border-radius:12px}
.card span{display:block;margin-top:24px;font-size:20px;font-weight:500;color:#222}

/* testimonials */
.reviews h2{left:0;top:2588px;width:1200px;text-align:center;font-size:46px}
.stars{left:0;top:2658px;width:1200px;display:flex;justify-content:center;gap:3px}
.quote{left:190px;top:2692px;width:820px;text-align:center;font-size:15px;line-height:24px;color:#333}
.avatar{left:490px;top:2880px;width:76px;height:76px;border-radius:50%;background:#8a9478}
.who{left:578px;top:2890px}
.who b{display:block;font-size:20px;font-weight:600;color:#222}
.who span{font-size:15px;color:#555}

/* contact */
.contact{left:0;top:3052px;width:1200px;height:538px;background:linear-gradient(180deg,var(--orange-soft) 0%,var(--orange) 45%,var(--orange-deep) 100%)}
.contact h2{left:0;top:90px;width:1200px;text-align:center;font-size:46px;color:var(--white)}
.bubble{position:absolute;top:156px;width:270px;height:270px;border-radius:50%;background:rgba(255,255,255,.12);text-align:center;color:var(--white);font-size:17px;line-height:22px}
.bubble .ic{margin:72px auto 0;width:68px;height:68px;border-radius:50%;background:var(--white);display:flex;align-items:center;justify-content:center}
.bubble p{margin:24px auto 0;width:230px}

/* clients */
.clients h2{left:0;top:3674px;width:1200px;text-align:center;font-size:46px}
.client{position:absolute;top:3750px;width:168px;height:74px;display:flex;align-items:center;justify-content:center;font-weight:700;font-size:20px;color:#222}
.client::before{content:"";position:absolute;inset:0;border:1.5px solid #bbb;transform:skewX(-8deg)}
.dots{left:0;top:3848px;width:1200px;display:flex;justify-content:center;gap:9px}
.dots i{width:10px;height:10px;border-radius:50%;background:#ccc}
.dots i.on{background:#111}

/* footer */
.footer{left:0;top:3900px;width:1200px;height:561px}
.footer .logo{left:114px;top:270px;font-size:32px}
.socials{left:150px;top:352px;display:flex;gap:12px}
.socials i{width:26px;height:26px;border-radius:50%;background:#555}
.socials i.on{background:var(--white)}
.f-title{font-size:19px;font-weight:600;color:var(--white)}
.info{left:502px;top:222px}
.info-row{position:absolute;left:0;display:flex;gap:18px;color:var(--white);width:250px}
.info-row b{display:block;font-size:14px;font-weight:600}
.info-row small{display:block;font-size:11px;line-height:15px;color:#ddd;margin-top:4px}
.links{top:228px;list-style:none;color:var(--white);font-size:14px}
.links li{height:32px;display:flex;align-items:center;gap:14px}
.copy{left:0;top:4408px;width:1200px;text-align:center;color:var(--white);font-size:14px}
</style>
</head>
<body>

<!-- top bar -->
<div class="abs topbar">
  <div class="abs left">ReviewHub based on 1606 reviews</div>
  <div class="abs right">
    <svg width="12" height="12" viewBox="0 0 24 24"><path fill="#fff" d="M6.6 10.8a15 15 0 0 0 6.6 6.6l2.2-2.2c.3-.3.7-.4 1-.2 1.1.4 2.3.6 3.6.6.6 0 1 .4 1 1V20c0 .6-.4 1-1 1A17 17 0 0 1 3 4c0-.6.4-1 1-1h3.5c.6 0 1 .4 1 1 0 1.3.2 2.5.6 3.6.1.3 0 .7-.2 1z"/></svg>
    <span>Call Us Today! 555-014-2290</span>
  </div>
</div>

<!-- navigation -->
<div class="abs nav">
  <div class="abs logo"><span class="mark"></span>TKFinanceMan</div>
  <div class="abs nav-links">
    <span class="active">Home</span><span>Why us</span><span>What we finance</span><span>Reviews</span><span>Contact</span>
  </div>
  <div class="btn">Apply Now</div>
</div>

<!-- hero -->
<section class="abs hero">
  <div class="abs hero-photo" role="img" aria-label="Sunset over a calm lake with orange sky"></div>
  <div class="abs hero-rv" role="img" aria-label="Class C motorhome on a road in front of snowy mountains"></div>
  <svg class="abs" style="left:0;top:0" width="1200" height="600" viewBox="0 0 1200 600">
    <path d="M0 420 C 170 620, 520 620, 740 540 C 900 480, 1050 420, 1200 470 L1200 600 L0 600 Z" fill="#fff"/>
    <path d="M0 400 C 150 590, 470 600, 720 520 C 560 585, 200 600, 0 440 Z" fill="var(--orange)"/>
  </svg>
  <h1 class="abs display">RV Loans<br>Made Easy!</h1>
  <p class="abs">Welcome to TKFinanceMan.com, your one-stop resource for all of your RV financing needs.</p>
  <div class="btn">Apply Today</div>
  <div class="arrow" style="left:145px;top:438px;width:38px;height:38px"><svg width="12" height="12" viewBox="0 0 12 12"><path d="M8 1 3 6l5 5" stroke="#111" stroke-width="1.8" fill="none"/></svg></div>
  <div class="arrow" style="left:192px;top:438px;width:38px;height:38px"><svg width="12" height="12" viewBox="0 0 12 12"><path d="m4 1 5 5-5 5" stroke="#111" stroke-width="1.8" fill="none"/></svg></div>
</section>

<!-- trusted source -->
<section class="trusted">
  <div class="abs trusted-img" role="img" aria-label="Luxury diesel pusher motorhome in front of a city skyline"></div>
  <h2 class="abs display">Your Trusted Source<br>for RV Financing.</h2>
  <ul class="abs ticks">
    <li><svg width="14" height="14" viewBox="0 0 14 14"><circle cx="7" cy="7" r="7" fill="var(--orange)"/><path d="m4 7 2 2 4-4" stroke="#fff" stroke-width="1.6" fill="none"/></svg>Loans from $25,000 - $5M</li>
    <li><svg width="14" height="14" viewBox="0 0 14 14"><circle cx="7" cy="7" r="7" fill="var(--orange)"/><path d="m4 7 2 2 4-4" stroke="#fff" stroke-width="1.6" fill="none"/></svg>Up to 25yrs old</li>
    <li><svg width="14" height="14" viewBox="0 0 14 14"><circle cx="7" cy="7" r="7" fill="var(--orange)"/><path d="m4 7 2 2 4-4" stroke="#fff" stroke-width="1.6" fill="none"/></svg>Same-Day Approvals</li>
    <li><svg width="14" height="14" viewBox="0 0 14 14"><circle cx="7" cy="7" r="7" fill="var(--orange)"/><path d="m4 7 2 2 4-4" stroke="#fff" stroke-width="1.6" fill="none"/></svg>Quick Funding</li>
    <li><svg width="14" height="14" viewBox="0 0 14 14"><circle cx="7" cy="7" r="7" fill="var(--orange)"/><path d="m4 7 2 2 4-4" stroke="#fff" stroke-width="1.6" fill="none"/></svg>Private Party or Dealer</li>
    <li><svg width="14" height="14" viewBox="0 0 14 14"><circle cx="7" cy="7" r="7" fill="var(--orange)"/><path d="m4 7 2 2 4-4" stroke="#fff" stroke-width="1.6" fill="none"/></svg>Best Rates in the Industry</li>
  </ul>
  <p class="abs">Our goal is to make your RV purchase as quick and stress-free as possible. Our numerous lender relationships allow us to offer competitive rates and terms with quick turn-around times.</p>
  <div class="btn">Learn More</div>
</section>

<!-- RV types -->
<section class="abs types">
  <svg class="abs" style="left:0;top:0" width="1200" height="620" viewBox="0 0 1200 620">
    <path d="M0 220 C 300 80, 700 20, 1000 50 C 1120 65, 1180 130, 1200 180 L1200 620 L0 620 Z" fill="var(--dark)"/>
    <path d="M0 215 C 300 60, 720 0, 1000 25 C 1130 40, 1190 110, 1200 180 C 1180 120, 1110 60, 1000 52 C 720 30, 300 85, 0 218 Z" fill="var(--orange)"/>
  </svg>
  <h2 class="abs display">We Finance All Types of RV's</h2>
  <div class="type" style="left:144px"><div class="pic" role="img" aria-label="Diesel pusher parked by a lake at dusk" style="background:linear-gradient(180deg,#9aa6ad,#b3956a)"></div><span>Diesel Pushers</span></div>
  <div class="type" style="left:386px"><div class="pic" role="img" aria-label="Class A motorhome among trees by a lake" style="background:linear-gradient(180deg,#8c9a9e,#5f6661)"></div><span>Class A</span></div>
  <div class="type" style="left:628px"><div class="pic" role="img" aria-label="Class B camper van by a mountain fjord" style="background:linear-gradient(180deg,#a7bccd,#8a9690)"></div><span>Class B</span></div>
  <div class="type" style="left:871px"><div class="pic" role="img" aria-label="Class C motorhome on green grass" style="background:linear-gradient(180deg,#b4c9d8,#9aae84)"></div><span>Class C</span></div>
  <div class="arrow line" style="left:43px;top:390px;width:52px;height:52px"><svg width="14" height="14" viewBox="0 0 12 12"><path d="M8 1 3 6l5 5" stroke="#fff" stroke-width="1.6" fill="none"/></svg></div>
  <div class="arrow line" style="left:1101px;top:390px;width:52px;height:52px"><svg width="14" height="14" viewBox="0 0 12 12"><path d="m4 1 5 5-5 5" stroke="#fff" stroke-width="1.6" fill="none"/></svg></div>
</section>

<!-- more than boats -->
<section class="abs more">
  <h2 class="abs display">We Finance More Than<br>Just Boats</h2>
  <p class="abs">At Meridian Recreational Finance, we are your one-stop resource for all marine, RV and Airplane Financing</p>
  <div class="btn">Contact Us</div>
</section>
<div class="card" style="left:144px"><div class="pic" role="img" aria-label="Orange speed boat racing on blue water" style="background:linear-gradient(180deg,#3aa3b4,#2a8296)"></div><span>Marine Financing</span></div>
<div class="card" style="left:457px"><div class="pic" role="img" aria-label="Pickup truck towing a fifth-wheel RV" style="background:linear-gradient(180deg,#8fa9c6,#7d8186)"></div><span>RV Financing</span></div>
<div class="card" style="left:771px"><div class="pic" role="img" aria-label="White private jet on the tarmac" style="background:linear-gradient(180deg,#a9cbea,#d3d8dd)"></div><span>Aircraft Financing</span></div>

<!-- testimonials -->
<section class="reviews">
  <h2 class="abs display">What Our Customers Say</h2>
  <div class="abs stars">
    <svg width="14" height="14" viewBox="0 0 24 24"><path fill="var(--orange)" d="M12 2l3 7 7 .6-5.3 4.7 1.6 7.2L12 17.8 5.7 21.5l1.6-7.2L2 9.6 9 9z"/></svg>
    <svg width="14" height="14" viewBox="0 0 24 24"><path fill="var(--orange)" d="M12 2l3 7 7 .6-5.3 4.7 1.6 7.2L12 17.8 5.7 21.5l1.6-7.2L2 9.6 9 9z"/></svg>
    <svg width="14" height="14" viewBox="0 0 24 24"><path fill="var(--orange)" d="M12 2l3 7 7 .6-5.3 4.7 1.6 7.2L12 17.8 5.7 21.5l1.6-7.2L2 9.6 9 9z"/></svg>
    <svg width="14" height="14" viewBox="0 0 24 24"><path fill="var(--orange)" d="M12 2l3 7 7 .6-5.3 4.7 1.6 7.2L12 17.8 5.7 21.5l1.6-7.2L2 9.6 9 9z"/></svg>
    <svg width="14" height="14" viewBox="0 0 24 24"><path fill="var(--orange)" d="M12 2l3 7 7 .6-5.3 4.7 1.6 7.2L12 17.8 5.7 21.5l1.6-7.2L2 9.6 9 9z"/></svg>
  </div>
  <p class="abs quote">"Just purchased a boat and used Meridian and they made the process very easy. Dana Whitfield helped every step of the way and was always available when I had any questions. She was quick to keep me updated and streamlined the entire process of paperwork and funding. I would highly recommend using Meridian based on my purchasing experience. Ask for Dana and she will not let you down will definitely use again when buying my next boat. Just purchased a boat and used Meridian and they made the process very easy. Dana Whitfield helped every step of the way and was always available when I had any questions. She was quick to keep me updated and streamlined the entire process"</p>
  <div class="arrow dark" style="left:46px;top:2751px;width:50px;height:50px"><svg width="14" height="14" viewBox="0 0 12 12"><path d="M8 1 3 6l5 5" stroke="#333" stroke-width="1.5" fill="none"/></svg></div>
  <div class="arrow dark" style="left:1102px;top:2751px;width:50px;height:50px"><svg width="14" height="14" viewBox="0 0 12 12"><path d="m4 1 5 5-5 5" stroke="#333" stroke-width="1.5" fill="none"/></svg></div>
  <div class="abs avatar" role="img" aria-label="Customer portrait"></div>
  <div class="abs who"><b>Carl Benton</b><span>Company name</span></div>
</section>

<!-- contact -->
<section class="abs contact">
  <h2 class="abs display">Contact Us</h2>
  <div class="bubble" style="left:144px">
    <div class="ic"><svg width="20" height="24" viewBox="0 0 20 24"><path fill="#111" d="M10 0a8 8 0 0 0-8 8c0 6 8 16 8 16s8-10 8-16a8 8 0 0 0-8-8zm0 11a3 3 0 1 1 0-6 3 3 0 0 1 0 6z"/></svg></div>
    <p>4410 Harbor Vista Rd Ste. 210, Bayview, CA 90210</p>
  </div>
  <div class="bubble" style="left:464px">
    <div class="ic"><svg width="24" height="18" viewBox="0 0 24 18"><rect width="24" height="18" rx="2" fill="#111"/><path d="m1 2 11 8 11-8" stroke="#fff" stroke-width="1.8" fill="none"/></svg></div>
    <p>reed@tkfinanceman.example</p>
  </div>
  <div class="bubble" style="left:783px">
    <div class="ic"><svg width="22" height="22" viewBox="0 0 24 24"><path fill="#111" d="M6.6 10.8a15 15 0 0 0 6.6 6.6l2.2-2.2c.3-.3.7-.4 1-.2 1.1.4 2.3.6 3.6.6.6 0 1 .4 1 1V20c0 .6-.4 1-1 1A17 17 0 0 1 3 4c0-.6.4-1 1-1h3.5c.6 0 1 .4 1 1 0 1.3.2 2.5.6 3.6.1.3 0 .7-.2 1z"/></svg></div>
    <p>(555) 014-2290</p>
  </div>
</section>

<!-- clients -->
<section class="clients">
  <h2 class="abs display">Our Clients</h2>
  <div class="client" style="left:148px">Ridgeway</div>
  <div class="client" style="left:334px">Trailcraft</div>
  <div class="client" style="left:520px">Nomadix</div>
  <div class="client" style="left:706px">Pinecrest</div>
  <div class="client" style="left:892px">Summitline</div>
  <div class="abs dots"><i></i><i class="on"></i><i></i></div>
</section>

<!-- footer -->
<footer class="abs footer">
  <svg class="abs" style="left:0;top:0" width="1200" height="561" viewBox="0 0 1200 561">
    <path d="M0 210 C 200 60, 520 20, 800 30 C 1000 40, 1150 90, 1200 140 L1200 561 L0 561 Z" fill="var(--dark)"/>
    <path d="M0 205 C 200 40, 520 0, 800 8 C 1000 15, 1160 70, 1200 140 C 1150 95, 1000 50, 800 44 C 520 38, 200 80, 0 215 Z" fill="var(--orange)"/>
  </svg>
  <div class="abs logo"><span class="mark"></span>TKFinanceMan</div>
  <div class="abs socials"><i></i><i class="on"></i><i></i></div>

  <div class="abs info">
    <div class="f-title" style="position:absolute;top:-30px;width:200px">CONTACT INFO</div>
    <div class="info-row" style="top:18px"><svg width="14" height="18" viewBox="0 0 20 24"><path fill="var(--orange)" d="M10 0a8 8 0 0 0-8 8c0 6 8 16 8 16s8-10 8-16a8 8 0 0 0-8-8zm0 11a3 3 0 1 1 0-6 3 3 0 0 1 0 6z"/></svg><div><b>Address</b><small>4410 Harbor Vista Rd Ste.<br>210, Bayview, CA 90210</small></div></div>
    <div class="info-row" style="top:88px"><svg width="18" height="14" viewBox="0 0 24 18"><rect width="24" height="18" rx="2" fill="var(--orange)"/><path d="m1 2 11 8 11-8" stroke="#262626" stroke-width="1.8" fill="none"/></svg><div><b>Email</b><small>tt@tkfinanceman.example</small></div></div>
    <div class="info-row" style="top:146px"><svg width="16" height="16" viewBox="0 0 24 24"><path fill="var(--orange)" d="M6.6 10.8a15 15 0 0 0 6.6 6.6l2.2-2.2c.3-.3.7-.4 1-.2 1.1.4 2.3.6 3.6.6.6 0 1 .4 1 1V20c0 .6-.4 1-1 1A17 17 0 0 1 3 4c0-.6.4-1 1-1h3.5c.6 0 1 .4 1 1 0 1.3.2 2.5.6 3.6.1.3 0 .7-.2 1z"/></svg><div><b>Phone</b><small>(555) 014-2290</small></div></div>
  </div>

  <div class="abs f-title" style="left:766px;top:192px">QUICK LINKS</div>
  <ul class="abs links" style="left:766px">
    <li><svg width="10" height="10" viewBox="0 0 10 10"><path d="m1 1 3 4-3 4M5 1l3 4-3 4" stroke="var(--orange)" stroke-width="1.4" fill="none"/></svg>Home</li>
    <li><svg width="10" height="10" viewBox="0 0 10 10"><path d="m1 1 3 4-3 4M5 1l3 4-3 4" stroke="var(--orange)" stroke-width="1.4" fill="none"/></svg>About</li>
    <li><svg width="10" height="10" viewBox="0 0 10 10"><path d="m1 1 3 4-3 4M5 1l3 4-3 4" stroke="var(--orange)" stroke-width="1.4" fill="none"/></svg>Services</li>
    <li><svg width="10" height="10" viewBox="0 0 10 10"><path d="m1 1 3 4-3 4M5 1l3 4-3 4" stroke="var(--orange)" stroke-width="1.4" fill="none"/></svg>Contact</li>
  </ul>
  <ul class="abs links" style="left:901px">
    <li><svg width="10" height="10" viewBox="0 0 10 10"><path d="m1 1 3 4-3 4M5 1l3 4-3 4" stroke="var(--orange)" stroke-width="1.4" fill="none"/></svg>Terms and Condition</li>
    <li><svg width="10" height="10" viewBox="0 0 10 10"><path d="m1 1 3 4-3 4M5 1l3 4-3 4" stroke="var(--orange)" stroke-width="1.4" fill="none"/></svg>Privacy policy</li>
    <li><svg width="10" height="10" viewBox="0 0 10 10"><path d="m1 1 3 4-3 4M5 1l3 4-3 4" stroke="var(--orange)" stroke-width="1.4" fill="none"/></svg>Help</li>
    <li><svg width="10" height="10" viewBox="0 0 10 10"><path d="m1 1 3 4-3 4M5 1l3 4-3 4" stroke="var(--orange)" stroke-width="1.4" fill="none"/></svg>Support</li>
  </ul>
</footer>
<div class="abs copy">© Copyrights 2024 | All Rights Reserved</div>

</body>
</html>
```